Trading Company needs a business card design, letter head design and email signature

We need a double-sided business card design, letter head design and an email signature. We have a logo design.

Possible Tag Lines:
• “Connecting Worlds, Building Excellence.”
• “Worldwide Reach, Trusted Quality.”
• “Bridging Borders, Building Quality.”
• “Worldwide Partnerships, Superior Goods.”
• “Where Quality Meets Affordability”

Services Offered:
Procurement
Fabrication
Distribution
Logistics
Import/Export

Requirements
Must have
• Nice quality double sided Business Card design, Letterhead design needs to be A4
Nice to have
• possible ideas on tag lines

```html
<!DOCTYPE html>
<html lang="en">
<head>
<meta charset="utf-8">
<title>Trivane Business Card</title>
<link href="https://fonts.googleapis.com/css2?family=Montserrat:wght@500;700;800&family=Roboto:wght@400;500&display=swap" rel="stylesheet">
<style>
  :root {
    --stage: #3a3a3a;
    --card-white: #ffffff;
    --card-black: #141414;
    --brand-red: #e42528;
    --ink-gray: #4a4b4d;
    --rule-gray: #6d6e70;
  }
  * { margin: 0; padding: 0; box-sizing: border-box; }
  html, body {
    width: 1200px; height: 1129px; overflow: hidden;
    background: var(--stage);
  }
  .stage { position: relative; width: 1200px; height: 1129px; }
  .card {
    position: absolute; left: 150px; width: 900px; height: 514px;
    overflow: hidden;
    box-shadow: 0 12px 30px rgba(0,0,0,.45);
  }
  /* Back side */
  .card-back { top: 34px; background: var(--card-black); }
  .back-pattern {
    position: absolute; inset: 0;
    background: linear-gradient(120deg, #6c6c6c 0%, #3c3c3c 35%, #1c1c1c 65%, #0e0e0e 100%);
    opacity: .55;
  }
  .back-mark {
    position: absolute; left: 640px; top: 236px;
    display: flex; align-items: center; gap: 12px;
  }
  .back-mark .mark-square { width: 34px; height: 34px; background: var(--brand-red); }
  .back-mark .mark-name {
    font-family: "Montserrat", sans-serif; font-weight: 800;
    font-size: 34px; letter-spacing: 2px; color: #ffffff;
  }
  /* Front side */
  .card-front { top: 581px; background: var(--card-white); }
  .brand {
    position: absolute; left: 110px; top: 110px; width: 330px;
    text-align: center;
  }
  .brand .mark-square {
    width: 92px; height: 92px; background: var(--brand-red);
    margin: 0 auto 22px;
  }
  .brand .brand-name {
    font-family: "Montserrat", sans-serif; font-weight: 800;
    font-size: 60px; letter-spacing: 3px; line-height: 1; color: var(--ink-gray);
  }
  .brand .tagline {
    margin-top: 10px;
    font-family: "Montserrat", sans-serif; font-weight: 700;
    font-size: 12.5px; letter-spacing: 1.6px; color: var(--ink-gray);
  }
  .divider {
    position: absolute; left: 472px; top: 80px; width: 2px; height: 270px;
    background: var(--rule-gray);
  }
  .contact {
    position: absolute; left: 505px; top: 78px;
    font-family: "Roboto", sans-serif; color: var(--ink-gray);
  }
  .person-name {
    font-family: "Montserrat", sans-serif; font-weight: 800;
    font-size: 31px; letter-spacing: .5px; line-height: 1.05;
  }
  .person-name .first { color: var(--brand-red); }
  .person-name .last { color: var(--ink-gray); }
  .person-title { font-size: 24px; margin-top: 2px; }
  .address { font-size: 23px; line-height: 1.25; margin-top: 22px; }
  .contact-list { list-style: none; margin-top: 8px; }
  .contact-list li {
    display: flex; align-items: center; gap: 10px;
    font-size: 23px; line-height: 1.35;
  }
  .contact-list svg { width: 22px; height: 22px; flex: none; }
  .services {
    position: absolute; left: 0; right: 0; top: 402px; text-align: center;
  }
  .services-title {
    font-family: "Montserrat", sans-serif; font-weight: 800;
    font-size: 21px; letter-spacing: 1.5px; color: var(--brand-red);
  }
  .services-list {
    list-style: none; display: flex; justify-content: center; gap: 18px;
    margin-top: 6px;
    font-family: "Roboto", sans-serif; font-size: 21px; color: var(--ink-gray);
  }
  .services-list li::before {
    content: "•"; color: var(--brand-red); margin-right: 5px;
  }
</style>
</head>
<body>
<main class="stage">

  <section class="card card-back" aria-label="Business card back">
    <div class="back-pattern" role="img" aria-label="Repeating embossed brand pattern in glossy grays fading to black"></div>
    <div class="back-mark">
      <span class="mark-square"></span>
      <span class="mark-name">TRIVANE</span>
    </div>
  </section>

  <section class="card card-front" aria-label="Business card front">
    <div class="brand">
      <div class="mark-square"></div>
      <div class="brand-name">TRIVANE</div>
      <div class="tagline">WORLDWIDE REACH, TRUSTED QUALITY</div>
    </div>

    <div class="divider"></div>

    <div class="contact">
      <h1 class="person-name"><span class="first">DELIA</span> <span class="last">MARROW</span></h1>
      <p class="person-title">Founder &amp; CEO</p>
      <p class="address">48 Harbor Lane Suite<br>7 Milford, MA 01757</p>
      <ul class="contact-list">
        <li>
          <svg viewBox="0 0 24 24" aria-hidden="true"><path fill="#e42528" d="M6.6 10.8a15.1 15.1 0 0 0 6.6 6.6l2.2-2.2a1 1 0 0 1 1-.25 11.4 11.4 0 0 0 3.6.57 1 1 0 0 1 1 1V20a1 1 0 0 1-1 1A17 17 0 0 1 3 4a1 1 0 0 1 1-1h3.5a1 1 0 0 1 1 1c0 1.25.2 2.45.57 3.57a1 1 0 0 1-.25 1z"/></svg>
          (555) 014-2290
        </li>
        <li>
          <svg viewBox="0 0 24 24" aria-hidden="true"><rect x="2.5" y="5" width="19" height="14" fill="none" stroke="#e42528" stroke-width="2"/><path d="M2.5 5l9.5 8 9.5-8M2.5 19l7-6.5M21.5 19l-7-6.5" fill="none" stroke="#e42528" stroke-width="2"/></svg>
          hello@trivanemail.com
        </li>
        <li>
          <svg viewBox="0 0 24 24" aria-hidden="true"><g fill="none" stroke="#e42528" stroke-width="1.6"><circle cx="12" cy="12" r="9.5"/><ellipse cx="12" cy="12" rx="4.2" ry="9.5"/><path d="M2.5 12h19M4 7h16M4 17h16"/></g></svg>
          www.trivaneweb.com
        </li>
      </ul>
    </div>

    <div class="services">
      <h2 class="services-title">SERVICES OFFERED</h2>
      <ul class="services-list">
        <li>Procurement</li>
        <li>Fabrication</li>
        <li>Distribution</li>
        <li>Logistics</li>
        <li>Import/Export</li>
      </ul>
    </div>
  </section>

</main>
</body>
</html>
```